Dog walking/Pet Sitting company needs a brochure to hook high end apartment tenants

We are looking for a brochure design that we can bring to meetings with high-end apartment and hotel management that will explain who we are, what we do, and how we can help their tenants/guests. I would like it to reflect the same look and feel of our website, carried over to printed brochure. Wesbite is www.hollowbrookpawcare.com. I can provide the stock images from the website if needed. A bi-fold brochure is ideal, unless you feel the information would fit better on a tri-fold. My company colors are #5D4664 and #5BA046. I would like a more professional tone to it, rather than fun.

Target Market(s)

Demo Professional Females and Males ages 30-50 with pets

Industry/Entity Type

Pet sitting

Font styles to use
Sans Serif

Colors
6b449b
9bcb3c

Requirements
Must have
• the same look and feel as my website; explain who we are, what we do, how we can help; include services offered; Mention that we service Maple Ridge and surrounding towns. Mention 15 years in business.
Should not have
• do not list pricing on brochure (you can mention pricing is available on the website). No cartoonish feel.

```html
<!DOCTYPE html>
<html lang="en">
<head>
<meta charset="utf-8">
<title>Hollowbrook Paw Care – Bi-fold Brochure</title>
<link rel="stylesheet" href="https://fonts.googleapis.com/css2?family=Montserrat:wght@500;600;700;800&family=Open+Sans:wght@400;600;700&display=swap">
<style>
:root{
  --purple:#5D4664;
  --purple-deep:#3f2d47;
  --purple-soft:#7a5c82;
  --green:#5BA046;
  --ink:#3a3340;
  --muted:#6f6876;
  --paper:#ffffff;
  --backdrop:#2b6f93;
}
*{box-sizing:border-box;margin:0;padding:0}
html,body{width:917px;height:1200px;overflow:hidden}
body{background:var(--backdrop);position:relative;font-family:"Open Sans",sans-serif;color:var(--ink)}
.spread{position:absolute;left:58px;width:800px;height:540px;display:flex;box-shadow:0 10px 30px rgba(0,0,0,.25)}
.spread--outer{top:40px}
.spread--inner{top:620px}
.page{position:relative;width:400px;height:540px;overflow:hidden;background:var(--paper)}
.photo{position:absolute;display:block}
.brand{display:flex;align-items:center;gap:6px}
.brand__dot{width:14px;height:14px;border-radius:50%;border:2px solid var(--purple)}
.brand__name{font-family:"Montserrat",sans-serif;font-weight:700;font-size:10px;color:var(--purple);letter-spacing:.04em;text-transform:uppercase}

/* Back cover */
.back{background:linear-gradient(160deg,var(--purple-soft) 0%,var(--purple) 45%,var(--purple-deep) 100%);color:#fff}
.about{position:absolute;left:30px;top:34px;width:340px}
.about__title{font-family:"Montserrat",sans-serif;font-weight:700;font-size:16px;color:var(--green);margin-bottom:8px}
.about p{font-size:6.8px;line-height:1.45;margin-bottom:6px;color:#f1ecf3}
.about__sign{font-size:6.8px;line-height:1.4;margin-top:4px}
.about__sign strong{font-weight:700}
.back .brand{position:absolute;right:30px;top:335px}
.back .brand__dot{border-color:#fff}
.back .brand__name{color:#fff;font-size:8px}
.back__photo{left:22px;top:410px;width:100px;height:120px;border-radius:6px;background:linear-gradient(180deg,#b99a7e,#6b4b3a)}
.contact{position:absolute;left:170px;top:440px;list-style:none}
.contact li{display:flex;align-items:center;gap:6px;font-size:7.5px;color:#fff;margin-bottom:5px}
.contact svg{width:9px;height:9px;flex:none}

/* Front cover */
.front .brand{position:absolute;right:28px;top:32px}
.front__ring{position:absolute;left:30px;top:80px}
.front__photo{left:68px;top:118px;width:264px;height:264px;border-radius:50%;background:radial-gradient(circle at 40% 40%,#f1e6dc,#c9b3a3 60%,#7d6c65)}
.tagline{position:absolute;left:40px;top:408px;width:330px;text-align:right;font-family:"Montserrat",sans-serif;font-weight:700;font-size:13px;line-height:1.3;color:var(--purple)}
.tagline em{display:block;font-style:normal;color:var(--green);font-size:14px}
.front__url{position:absolute;right:30px;top:470px;font-size:8px;color:var(--muted)}

/* Inner pages */
.services-left{background:var(--purple)}
.services-left .bgshape,.services-right .bgshape{position:absolute;left:0;top:0}
.pill{position:absolute;left:150px;top:24px;width:250px;height:42px;background:var(--purple);border-radius:21px 0 0 21px;color:#fff;font-family:"Montserrat",sans-serif;font-weight:800;font-size:11.5px;line-height:1.15;padding:8px 0 0 26px;letter-spacing:.03em}
.col{position:absolute}
.col--left{left:40px;top:74px;width:255px}
.col--right{left:30px;top:36px;width:292px}
.svc{margin-bottom:5px}
.svc__title{font-family:"Montserrat",sans-serif;font-weight:700;font-size:9px;color:var(--green);margin-bottom:2px}
.svc p{font-size:5.8px;line-height:1.32;margin-bottom:2px}
.svc ul{list-style:none}
.svc li{font-size:5.8px;line-height:1.32;padding-left:7px;position:relative}
.svc li::before{content:"";position:absolute;left:0;top:2px;width:3.5px;height:3.5px;border-radius:50%;background:var(--green)}
.svc--narrow{width:250px}
.round{border-radius:50%;border:3px solid #fff;box-shadow:0 0 0 2px var(--purple)}
.round--ball{left:308px;top:160px;width:62px;height:62px;background:radial-gradient(circle,#e8d3a8,#b98e4e)}
.round--pup{left:308px;top:300px;width:62px;height:62px;background:radial-gradient(circle,#f4efe8,#b9c8b0)}
.couch{left:0;top:432px;width:200px;height:70px;background:linear-gradient(120deg,#8f8ea0,#c9b3c7 50%,#7a7488)}
.area-box{position:absolute;left:205px;top:446px;width:178px;height:62px;background:var(--purple);border-radius:10px 0 0 10px;color:#fff;padding:9px 12px;font-family:"Montserrat",sans-serif;font-weight:600;font-size:8.5px;line-height:1.3}
.area-box small{display:block;font-family:"Open Sans",sans-serif;font-weight:400;font-size:6.5px;margin-top:4px;color:#e8dfeb}
.round--cat{left:334px;top:206px;width:60px;height:60px;background:radial-gradient(circle,#e4ddd6,#a8988c)}
.hug{left:282px;top:420px;width:118px;height:118px;border-radius:60px 0 0 0;background:linear-gradient(150deg,#efe2d6,#c79e7c 60%,#7c5a45)}
</style>
</head>
<body>

<section class="spread spread--outer">
  <article class="page back">
    <div class="about">
      <h2 class="about__title">About Us</h2>
      <p>We specialize in one-to-one personalized, quality pet care. We offer many services to cater to your needs. Whether you have dogs, cats, reptiles or rodents, we can help!</p>
      <p>Our business was born out of necessity. Fifteen years ago, as a busy professional with a new puppy, I struggled to find reliable care that fit long workdays and travel. I knew other owners felt the same guilt, worry and fear about leaving their pets behind.</p>
      <p>I imagined a company that could provide peace of mind for pet owners, giving them the freedom to focus on their careers, families and lives while knowing their companions are cared for by trusted, trained professionals. With hard work and long hours, that vision became a reality.</p>
      <p>Today, we are a fully staffed company with employees, not independent contractors, who are insured, bonded and continually trained in pet first aid and behavior. We take pride in giving every pet the same love and attention we give our own.</p>
      <p>If you have pets and experience any feelings of guilt when you need to leave them behind, reach out to us! We pick right up where you leave off, with smiles, love and adventures that can turn an ordinary day extraordinary!</p>
      <p class="about__sign"><strong>Dana Whitfield,</strong><br>Owner, Hollowbrook Paw Care LLC</p>
    </div>
    <div class="brand"><span class="brand__dot"></span><span class="brand__name">Hollowbrook Paw Care</span></div>
    <div class="photo back__photo" role="img" aria-label="Photo of a small terrier holding a leather leash in its mouth"></div>
    <ul class="contact">
      <li><svg viewBox="0 0 24 24"><path fill="#5BA046" d="M6.6 10.8a15 15 0 0 0 6.6 6.6l2.2-2.2a1 1 0 0 1 1-.25 11.4 11.4 0 0 0 3.6.57 1 1 0 0 1 1 1V20a1 1 0 0 1-1 1A17 17 0 0 1 3 4a1 1 0 0 1 1-1h3.5a1 1 0 0 1 1 1c0 1.25.2 2.45.57 3.57a1 1 0 0 1-.25 1z"/></svg>201-555-0148</li>
      <li><svg viewBox="0 0 24 24"><rect x="2" y="5" width="20" height="14" rx="2" fill="none" stroke="#5BA046" stroke-width="2"/><path d="M2 6l10 7 10-7" fill="none" stroke="#5BA046" stroke-width="2"/></svg>hello@hollowbrookpawcare.com</li>
      <li><svg viewBox="0 0 24 24"><circle cx="12" cy="12" r="9" fill="none" stroke="#5BA046" stroke-width="2"/><path d="M3 12h18M12 3c3 3 3 15 0 18M12 3c-3 3-3 15 0 18" fill="none" stroke="#5BA046" stroke-width="1.6"/></svg>www.hollowbrookpawcare.com</li>
    </ul>
  </article>

  <article class="page front">
    <div class="brand"><span class="brand__dot"></span><span class="brand__name">Hollowbrook Paw Care</span></div>
    <svg class="front__ring" width="340" height="340" viewBox="0 0 340 340" aria-hidden="true">
      <circle cx="170" cy="170" r="150" fill="none" stroke="#5D4664" stroke-width="7" stroke-dasharray="640 302" transform="rotate(100 170 170)"/>
      <circle cx="170" cy="170" r="160" fill="none" stroke="#5BA046" stroke-width="3" stroke-dasharray="260 746" transform="rotate(-80 170 170)"/>
    </svg>
    <div class="photo front__photo" role="img" aria-label="Photo of a woman on a sofa cuddling a small black and white dog"></div>
    <p class="tagline">Prioritize Your Family, Career, Health, Social Life, Goals, Yourself.<em>We'll Focus on Your Pets.</em></p>
    <p class="front__url">www.hollowbrookpawcare.com</p>
  </article>
</section>

<section class="spread spread--inner">
  <article class="page services-left">
    <svg class="bgshape" width="400" height="540" viewBox="0 0 400 540" aria-hidden="true">
      <circle cx="255" cy="300" r="318" fill="#fff"/>
      <circle cx="255" cy="300" r="326" fill="none" stroke="#fff" stroke-width="2"/>
    </svg>
    <h2 class="pill">PROFESSIONAL<br>PET CARE SERVICES</h2>
    <div class="col col--left">
      <section class="svc">
        <h3 class="svc__title">Dog Walking</h3>
        <p>We are pleased to provide dog walking services Monday–Friday between the hours of 10:00 am and 3:00 pm.</p>
        <ul>
          <li>Walking your dog (we offer a standard untimed visit and a guaranteed one-hour visit)</li>
          <li>Providing healthy exercise and fun</li>
          <li>Cleaning your dog after coming in from outside</li>
          <li>Feeding your dog and/or providing fresh water/treats</li>
          <li>Training reinforcement</li>
          <li>Grooming &amp; pampering your dog, such as brushing out coat</li>
          <li>Light pet-related housekeeping (cleaning up accidents or food/water spills)</li>
          <li>Bringing in your mail/packages</li>
          <li>Providing you with an emailed/texted report along with photos</li>
        </ul>
      </section>
      <section class="svc">
        <h3 class="svc__title">Pet Sitting</h3>
        <p>We are pleased to provide pet sitting services 7 days a week during the following times: 7:30 am – 9:30 am, 12:00 pm – 4:00 pm, 7:30 pm – 9:30 pm.</p>
        <ul>
          <li>Three untimed visits throughout the day (morning, afternoon, evening) to ensure a happy and comfortable pet</li>
          <li>Inclusive of all pets within the household</li>
          <li>Walking your dog and playing with your cat or other household pets</li>
          <li>Providing healthy, fun exercise</li>
          <li>Cleaning your dog after coming in from outside</li>
          <li>Feeding your dog &amp; providing fresh water/treats</li>
          <li>Emailed visit reports and pictures of your pets</li>
          <li>Pet sitting visits also include home care at no additional cost: bringing in mail/packages, taking out the trash, watering plants, etc.</li>
        </ul>
      </section>
    </div>
    <div class="photo round round--ball" role="img" aria-label="Photo of a yellow Labrador holding a blue toy"></div>
    <div class="photo round round--pup" role="img" aria-label="Photo of a white puppy wearing a blue collar"></div>
    <div class="photo couch" role="img" aria-label="Photo of a woman relaxing on a sofa with her dog"></div>
    <div class="area-box">We service Maple Ridge &amp; surrounding towns. 15 years in business.<small>www.hollowbrookpawcare.com</small></div>
  </article>

  <article class="page services-right">
    <svg class="bgshape" width="400" height="540" viewBox="0 0 400 540" aria-hidden="true">
      <rect width="400" height="540" fill="#5D4664"/>
      <circle cx="140" cy="250" r="318" fill="#fff"/>
      <circle cx="140" cy="250" r="326" fill="none" stroke="#fff" stroke-width="2"/>
    </svg>
    <div class="col col--right">
      <section class="svc">
        <h3 class="svc__title">Cat Sitting / Small Pet Sitting</h3>
        <ul>
          <li>One untimed visit per day (we stay until your cat is content!)</li>
          <li>Socializing and playing with your cat</li>
          <li>Providing healthy mental stimulation and play</li>
          <li>Scooping litter box daily and full cleaning as needed</li>
          <li>Feeding your cat, providing fresh water/treats and cleaning the feeding area</li>
          <li>Emailed visit reports and pictures of your pet</li>
          <li>Cat sitting visits also include basic home care at no additional cost. This may include bringing in the mail and packages, taking out the trash, sweeping the floors, watering plants, etc.</li>
        </ul>
      </section>
      <section class="svc">
        <h3 class="svc__title">Day Care &amp; Overnight Boarding</h3>
        <p>We understand that leaving your dog at home or in a kennel is not always the best option. That's why we offer boarding in our home. We accept smaller breed dogs (approximately 30lbs or less) who are fully house-trained, neutered/spayed, and socialize well with other dogs. All vaccinations must be current, including rabies, DHLPP and Bordetella.</p>
        <p>While staying in our home, your dog will enjoy walks by the lake, playtime in our fenced-in yard, and lounging on the couch with us. We limit the number of guests to maintain a calm atmosphere. We do not crate your dog unless you specify. Please provide their food and whatever else will make their stay more comfortable!</p>
      </section>
      <section class="svc">
        <h3 class="svc__title">Sleepovers</h3>
        <p>Our newest option is becoming increasingly popular with pet parents who want to leave their pets home, but not alone overnight. A sitter stays with your pets in the comfort of your home (from 10 pm to 7 am). This option includes a late-night walk and an early morning walk. Midday care can be added while you are away. It includes care for all pets in your household.</p>
      </section>
      <section class="svc svc--narrow">
        <h3 class="svc__title">Wedding Attendant</h3>
        <p>When they are a part of your family, they should also be a part of your wedding! Our attendant will groom your pet, bring them to and from the venue, keep them calm and happy, and walk them down the aisle at the perfect moment. Every detail is customized, and we work with your coordinator so nothing is overlooked. Check out our blog for a behind-the-scenes look at a recent wedding we attended!</p>
      </section>
    </div>
    <div class="photo round round--cat" role="img" aria-label="Photo of a grey cat being petted"></div>
    <div class="photo hug" role="img" aria-label="Photo of a smiling woman hugging a young shepherd dog"></div>
  </article>
</section>

</body>
</html>
```